BOLD & MINIMALIST DESIGN NEEDED

We want a very bold but minimalistic business card design that is impactful and utilizes both sides of the business card. Our current logo is included for your use.

We want bold fonts and good use of negative space. We don't want the logo to overpower the design.

Target Market(s)

Professionals who are building new commercial buildings.

Industry/Entity Type

Construction

Contact Information for Business Card

Name, Title, email, office phone, cell phone, website

Font styles to use
Serif
Sans Serif

Requirements
Must have
• Bold design!

```html
<!DOCTYPE html>
<html lang="en">
<head>
<meta charset="utf-8">
<title>Ridgeline Build — Business Card</title>
<link href="https://fonts.googleapis.com/css2?family=Montserrat:wght@400;500;700;800&display=swap" rel="stylesheet">
<style>
  :root {
    --backdrop: #dcdcdc;
    --paper: #ffffff;
    --ink: #0c0d0f;
    --green: #8ccf4d;
    --green-deep: #6cc04a;
    --grey-text: #6f6f6f;
  }
  * { margin: 0; padding: 0; box-sizing: border-box; }
  html, body {
    width: 1200px; height: 1200px; overflow: hidden;
    background: var(--backdrop);
    font-family: "Montserrat", sans-serif;
  }
  .card {
    position: absolute; left: 179px; width: 861px; height: 496px;
    background: var(--paper); overflow: hidden;
  }
  .card--front { top: 84px; }
  .card--back { top: 622px; }

  .brand {
    display: flex; align-items: center; gap: 14px;
    font-weight: 800; letter-spacing: 1px; text-transform: uppercase;
    white-space: nowrap;
  }
  .brand__square { width: 26px; height: 26px; background: var(--green-deep); flex: none; }

  .card--front .brand {
    position: absolute; left: 0; right: 0; top: 220px;
    justify-content: center; font-size: 46px; color: var(--ink);
  }

  .back-shape { position: absolute; inset: 0; width: 100%; height: 100%; }

  .card--back .brand--lead {
    position: absolute; left: 43px; top: 62px;
    font-size: 36px; color: var(--paper);
  }
  .card--back .brand--mark {
    position: absolute; left: 522px; top: 150px; width: 300px;
    flex-direction: column; gap: 12px;
    font-size: 24px; color: var(--ink);
  }
  .brand--mark .brand__square { width: 60px; height: 60px; }

  .holder {
    position: absolute; right: 48px; top: 285px; text-align: right;
  }
  .holder__name { font-size: 36px; font-weight: 700; color: var(--ink); letter-spacing: 0.5px; }
  .holder__title { font-size: 26px; font-weight: 400; color: var(--grey-text); letter-spacing: 1px; margin-top: 2px; }

  .contact {
    position: absolute; top: 405px; display: flex; flex-direction: column; gap: 10px;
    font-size: 23px; color: var(--grey-text); letter-spacing: 1.5px;
  }
  .contact--phones { left: 156px; }
  .contact--web { right: 46px; align-items: flex-end; }
  .contact__row { display: flex; align-items: center; gap: 14px; height: 25px; }
  .contact__icon { width: 24px; height: 24px; flex: none; }
  .contact__accent { color: var(--green-deep); }
</style>
</head>
<body>

<section class="card card--front">
  <div class="brand"><span class="brand__square"></span>Ridgeline Build</div>
</section>

<section class="card card--back">
  <svg class="back-shape" viewBox="0 0 1387 798" preserveAspectRatio="none" aria-hidden="true">
    <rect width="1387" height="798" fill="var(--ink)"/>
    <polygon points="0,646 1085,52 1387,215 1387,798 0,798" fill="var(--green)"/>
    <polygon points="110,586 1085,92 1387,222 1387,798 0,798 0,646" fill="var(--paper)"/>
  </svg>

  <div class="brand brand--lead">Ridgeline Build</div>
  <div class="brand brand--mark"><span class="brand__square"></span>Ridgeline Build</div>

  <div class="holder">
    <div class="holder__name">Name Surename</div>
    <div class="holder__title">Director</div>
  </div>

  <div class="contact contact--phones">
    <div class="contact__row">
      <svg class="contact__icon" viewBox="0 0 24 24" aria-hidden="true">
        <path d="M6.6 10.8a15 15 0 0 0 6.6 6.6l2.2-2.2a1 1 0 0 1 1-.25 11.4 11.4 0 0 0 3.6.6 1 1 0 0 1 1 1V20a1 1 0 0 1-1 1A17 17 0 0 1 3 4a1 1 0 0 1 1-1h3.5a1 1 0 0 1 1 1c0 1.25.2 2.45.6 3.6a1 1 0 0 1-.25 1z" fill="var(--ink)"/>
        <path d="M14 3a7 7 0 0 1 7 7M14 6.5A3.5 3.5 0 0 1 17.5 10" stroke="var(--ink)" stroke-width="1.8" fill="none"/>
      </svg>
      <span>555-014-2200</span>
    </div>
    <div class="contact__row">
      <svg class="contact__icon" viewBox="0 0 24 24" aria-hidden="true">
        <path d="M2 9c0-3 4-5 10-5s10 2 10 5v1h-5V8H7v2H2z" fill="var(--ink)"/>
        <path d="M5 12h14l2 9H3z" fill="var(--ink)"/>
        <circle cx="12" cy="16" r="2.4" fill="var(--paper)"/>
      </svg>
      <span>555-014-2200</span>
    </div>
  </div>

  <div class="contact contact--web">
    <div class="contact__row">
      <span>info@ridgeline-db.com</span>
      <svg class="contact__icon" viewBox="0 0 24 24" aria-hidden="true">
        <rect x="1" y="5" width="22" height="15" fill="var(--ink)"/>
        <path d="M2 6l10 8 10-8M2 19l7-6M22 19l-7-6" stroke="var(--paper)" stroke-width="1.4" fill="none"/>
      </svg>
    </div>
    <div class="contact__row">
      <span>www.<span class="contact__accent">ridgeline-db</span>.com</span>
      <svg class="contact__icon" viewBox="0 0 24 24" aria-hidden="true">
        <g stroke="var(--ink)" stroke-width="1.6" fill="none">
          <circle cx="12" cy="12" r="10"/>
          <ellipse cx="12" cy="12" rx="4.5" ry="10"/>
          <path d="M2 12h20M4 6.5h16M4 17.5h16M12 2v20"/>
        </g>
      </svg>
    </div>
  </div>
</section>

</body>
</html>
```